Catalogue Design Project

We need a catalog design for a new private university called Redwell Institute Bayshore (see website www.rwi-bs.org). The catalog should be about 30 pages maximum and will include items such as General Information, Academic schedule, department descriptions, program descriptions, course descriptions, school policies, student services, admissions, San diego Lifestyle, etc.
I will provide the text but I need a professional design with regard to page layouts. I have provided some examples.
Ok, i posted the catalog content, just missing course descriptions.
Target Market(s)
Young Professionals, Foreign Students
Industry/Entity Type
University
Look and feel
Each slider illustrates characteristics of the customer's brand and the style your logo design should communicate.

```html
<!DOCTYPE html>
<html lang="en">
<head>
<meta charset="utf-8">
<title>Admissions – Redwell Institute Bayshore</title>
<link rel="stylesheet" href="https://fonts.googleapis.com/css2?family=Carlito:wght@400;700&display=swap">
<style>
  :root {
    --ink: #1a1a1a;
    --brand-blue: #1d5a96;
    --brand-blue-dark: #164a7e;
    --rule-grey: #b9bcc0;
    --footer-grey: #8d9094;
    --paper: #ffffff;
  }
  * { margin: 0; padding: 0; box-sizing: border-box; }
  html, body { width: 927px; height: 1200px; overflow: hidden; background: var(--paper); }
  body { font-family: "Carlito", "Calibri", sans-serif; color: var(--ink); }
  .page { position: relative; width: 927px; height: 1200px; overflow: hidden; }

  .brand-mark {
    position: absolute; left: 58px; top: 40px;
    display: flex; align-items: center; gap: 10px;
    color: var(--brand-blue); font-size: 20px; font-weight: 700; line-height: 24px;
  }
  .brand-mark-dot { width: 16px; height: 16px; border-radius: 50%; background: var(--brand-blue); }

  .header-art {
    position: absolute; right: 0; top: 0; width: 330px; height: 108px;
    background: radial-gradient(ellipse at 70% 40%, #e4edf6 0%, #f1f5fa 45%, rgba(255,255,255,0) 75%);
  }
  .header-rule { position: absolute; left: 0; top: 110px; width: 927px; height: 1px; background: var(--rule-grey); }
  .section-tab { position: absolute; left: 660px; top: 102px; }
  .section-tab-label {
    position: absolute; left: 718px; top: 104px; width: 180px; height: 36px;
    color: #fff; font-size: 29px; line-height: 36px; letter-spacing: 0.5px; text-align: center;
  }

  .page-title {
    position: absolute; left: 0; top: 156px; width: 927px;
    text-align: center; font-size: 27px; font-weight: 700;
  }
  .intro, .block {
    position: absolute; left: 80px; width: 768px;
    font-size: 16.6px; text-align: justify;
  }
  .intro { top: 188px; line-height: 31.7px; }
  .block h2 {
    font-size: 19px; font-weight: 400; text-decoration: underline;
    text-underline-offset: 3px; line-height: 24px; margin-bottom: 1px;
  }
  .block p { line-height: 22.5px; }
  .block strong { font-weight: 700; }
  .block-apply { top: 382px; }
  .block-transcripts { top: 602px; }
  .block-credits { top: 781px; }
  .block-letters { top: 893px; }
  .block-international { top: 995px; }

  .footer-rule { position: absolute; left: 0; top: 1153px; width: 927px; height: 1px; background: var(--rule-grey); }
  .folio {
    position: absolute; right: 40px; top: 1168px;
    font-size: 13px; color: var(--footer-grey); letter-spacing: 0.3px;
  }
</style>
</head>
<body>
<div class="page">
  <div class="brand-mark"><span class="brand-mark-dot" aria-hidden="true"></span>Redwell Institute Bayshore</div>
  <div class="header-art" role="img" aria-label="Soft faded campus imagery in pale blue"></div>
  <div class="header-rule"></div>
  <svg class="section-tab" width="267" height="40" viewBox="0 0 267 40" aria-hidden="true">
    <polygon points="14,0 267,0 267,40 0,40" fill="var(--brand-blue)"/>
    <rect x="0" y="36" width="267" height="4" fill="var(--brand-blue-dark)"/>
  </svg>
  <div class="section-tab-label">ADMISSIONS</div>

  <h1 class="page-title">Admissions</h1>
  <p class="intro">MBA applicants who have or will obtain a bachelor’s degree from a regionally accredited institution in the U.S. or a comparable degree from an officially recognized college or university outside the U.S. may apply for admission. Certificate applicants need only proof of high school graduation, GED, or foreign equivalent. To ensure your application is processed efficiently, please submit your completed application and applicable documents no later than the application deadline (see university for current deadline) in order to be enrolled for the next available quarter or session.</p>

  <section class="block block-apply">
    <h2>How to Apply</h2>
    <p><strong>Step1:</strong> Visit RWIB's website and fill out the online application, which can be found at the following web address: http://www.rwi-bs.org/index.php/admissions/apply-today<br>
    <strong>Step2:</strong> After an admissions advisor contacts you after reviewing your application, you will be requested to submit the required documents for your program. The MBA program requires a copy of a diploma and an official transcript demonstrating all coursework and final GPA of a bachelor degree. Coursework must include Calculus. Certificate programs typically require proof of high school graduation. Both programs require 2 letters of recommendation.<br>
    <strong>Step3:</strong> Receive your acceptance letter and information regarding the next enrollment session.</p>
  </section>

  <section class="block block-transcripts">
    <h2>Official Transcripts</h2>
    <p>Any transcripts or academic documentation of coursework uploaded through our online application system or emailed to an academic advisor will serve as a temporary meeting of requirements, however an official, certified and sealed transcript must be sent to RWIB directly from the issuing institution. Please direct official bachelor and high school transcript questions to our University Admissions office at 619-555-0142. Redwell Institute Bayshore reserves the right to require the submission of official transcripts or credentials any time during the admission review process.</p>
  </section>

  <section class="block block-credits">
    <h2>Credits</h2>
    <p>RWIB generally accepts graduate level coursework taken at another institution to meet certain requirements for the Master of Business Administration degree program. Please consult a university advisor for more details. Certificate programs are not eligible for credit transfers.</p>
  </section>

  <section class="block block-letters">
    <h2>Letters of Recommendation</h2>
    <p>All programs require at least 2 letters of recommendations from friends, associates, business contacts, or qualified persons to adequately provide unbiased documentation on you. Letters need not be official and can be submitted through the online application process or emailed directly to an admissions advisor.</p>
  </section>

  <section class="block block-international">
    <h2>International Students</h2>
    <p>In addition to the requirements listed above, international students applying to any of our certificate programs or MBA must provide translated documents. Translations must be from a recognized official translating agency. Feel free to contact an advisor for a list of approved translating agencies. International students must also provide a proof of passing an English fluency examination such as EFLT, Kingsbridge, or other equivalent.</p>
  </section>

  <div class="footer-rule"></div>
  <div class="folio">19::: REDWELL INSTITUTE</div>
</div>
</body>
</html>
```